KRV Photography Business Card Design

I would like a business card designed in the shape of a camera.
Would like to see various camera designs. Would like to see what the card looks like in different colors. Would like to see which logo looks better on the various camera designs so please show me some with the white logo and some with the black logo. If you need a different file formats please let me know.
Project Deadline Extended Reason: My grandfather passed away and dealing with funeral plans so need to extend deadline. Added Tuesday, March 1, 2016
Project Deadline Extended
Reason: I just got back from out of town. My grandfather's passing was the primary focus for me these past few weeks and the funeral is over so now I will concentrate on picking my business card design. I really appreciate each designer who has taken the time to submit a design. Your effort has not gone unnoticed. I look forward to seeing more amazing designs.
Business
Contact Information for Business Card
Dorine
555-418-2706
https://www.facebook.com/krvphotographyfreelance/
MonaDorine@krv-photography.example

```html
<!DOCTYPE html>
<html lang="en">
<head>
<meta charset="UTF-8">
<title>KRV Photography Business Cards</title>
<link href="https://fonts.googleapis.com/css2?family=Cinzel:wght@400&family=Open+Sans:wght@400;700&display=swap" rel="stylesheet">
<style>
  :root {
    --backdrop: #bdbec0;
    --card: #000000;
    --gold: #d2a03a;
    --gold-deep: #c7852c;
    --white: #ffffff;
  }
  html, body { margin: 0; padding: 0; overflow: hidden; }
  body {
    width: 1200px; height: 927px;
    background: var(--backdrop);
    position: relative;
    font-family: "Open Sans", sans-serif;
  }
  .camera-card {
    position: absolute; top: 265px;
    width: 538px; height: 396px;
    filter: drop-shadow(6px 8px 7px rgba(0,0,0,0.35));
  }
  .camera-card--gold { left: 43px; }
  .camera-card--white { left: 618px; }
  .shutter-button, .viewfinder {
    position: absolute; background: var(--card); border-radius: 8px 8px 0 0;
  }
  .shutter-button { left: 70px; top: 18px; width: 63px; height: 20px; }
  .viewfinder { left: 379px; top: 0; width: 104px; height: 40px; border-radius: 10px 10px 0 0; }
  .card-body {
    position: absolute; left: 0; top: 24px; width: 538px; height: 372px;
    background: var(--card); border-radius: 22px;
  }
  .brand-mark {
    position: absolute; left: 227px; top: 29px; width: 84px; height: 84px;
    border-radius: 50%;
    background: linear-gradient(135deg, #f2d27a, #c99a2e 55%, #8f6614);
  }
  .brand-name {
    position: absolute; left: 0; right: 0; top: 123px; text-align: center;
    font-family: "Cinzel", serif; font-size: 25px; color: var(--gold);
    letter-spacing: 0.5px; margin: 0; font-weight: 400;
  }
  .name-rule {
    position: absolute; left: 0; right: 0; top: 238px; height: 1px;
    background: var(--accent);
  }
  .person-name {
    position: absolute; left: 50%; transform: translateX(-50%); top: 220px;
    padding: 0 3px; background: var(--card);
    font-weight: 700; font-size: 25px; letter-spacing: 2.5px; color: var(--accent);
    margin: 0; white-space: nowrap;
  }
  .contact-icons {
    position: absolute; left: 0; right: 0; top: 290px; text-align: center;
  }
  .contact-icons svg { width: 14px; height: 14px; margin: 0 1px; }
  .contact-lines {
    position: absolute; left: 0; right: 0; top: 312px; text-align: center;
    font-size: 15px; line-height: 19px; letter-spacing: 1px; color: var(--accent);
  }
  .contact-lines p { margin: 0; }
  .camera-card--gold { --accent: var(--gold-deep); }
  .camera-card--white { --accent: var(--white); }
</style>
</head>
<body>
  <div class="camera-card camera-card--gold">
    <div class="shutter-button"></div>
    <div class="viewfinder"></div>
    <div class="card-body">
      <div class="brand-mark"></div>
      <h1 class="brand-name">KRV Photography</h1>
      <div class="name-rule"></div>
      <h2 class="person-name">THEO MARLOW</h2>
      <div class="contact-icons">
        <svg viewBox="0 0 16 16" fill="none" stroke="currentColor" stroke-width="1.4" style="color:var(--accent)"><path d="M4 2l2.5 3-1.5 1.5c.8 2 2.3 3.5 4.5 4.5L11 9.5l3 2.5-1.5 2C7 13.5 2.5 9 2 3.5z"/></svg>
        <svg viewBox="0 0 16 16" fill="none" stroke="currentColor" stroke-width="1.4" style="color:var(--accent)"><rect x="1.5" y="3.5" width="13" height="9"/><path d="M1.5 3.5L8 9l6.5-5.5"/></svg>
      </div>
      <div class="contact-lines">
        <p>+330 5550-1942</p>
        <p>theo@marlowmail.example</p>
      </div>
    </div>
  </div>

  <div class="camera-card camera-card--white">
    <div class="shutter-button"></div>
    <div class="viewfinder"></div>
    <div class="card-body">
      <div class="brand-mark"></div>
      <h1 class="brand-name">KRV Photography</h1>
      <div class="name-rule"></div>
      <h2 class="person-name">THEO MARLOW</h2>
      <div class="contact-icons">
        <svg viewBox="0 0 16 16" fill="none" stroke="currentColor" stroke-width="1.4" style="color:var(--accent)"><path d="M4 2l2.5 3-1.5 1.5c.8 2 2.3 3.5 4.5 4.5L11 9.5l3 2.5-1.5 2C7 13.5 2.5 9 2 3.5z"/></svg>
        <svg viewBox="0 0 16 16" fill="none" stroke="currentColor" stroke-width="1.4" style="color:var(--accent)"><rect x="1.5" y="3.5" width="13" height="9"/><path d="M1.5 3.5L8 9l6.5-5.5"/></svg>
      </div>
      <div class="contact-lines">
        <p>+330 5550-1942</p>
        <p>theo@marlowmail.example</p>
      </div>
    </div>
  </div>
</body>
</html>
```